Business Card Design

I'm a commercial general contractor remodel offices, hotels, health clubs and stores mostly San Francisco and the peninsula
the file I down loaded is kind of what I want I like the I beam with my company name in it, that would be fine with me but if you have better Idea will look at it you never know, I'm decided to give in and change my company name to how every one knows me, I have been in business since 1991, I like the I beam logo I included one of my old card from my old company for reference for you.

BROCK CONSTRUCTION (is my company name)
Warren Pelkey contractor, LIc 514387
3148 Larkspur Row, San Bruno, California 94071
mobile, (415) 736-4052
phone (650) 514-2087
Fax, (650) 514-2088
email, brock@brockconstruction.example

```html
<!DOCTYPE html>
<html lang="en">
<head>
<meta charset="utf-8">
<title>Brock Construction – Business Card</title>
<link rel="stylesheet" href="https://fonts.googleapis.com/css2?family=Source+Sans+3:wght@400;600;700&display=swap">
<style>
  :root {
    --backdrop: #e9e7e3;
    --card-top: #f4f4f5;
    --card-bottom: #c4c6c9;
    --skyline: #d3d5d8;
    --band: #1f2022;
    --accent: #1f9be0;
    --ink: #55585c;
    --ink-soft: #8a8d91;
    --band-text: #c9cbce;
  }
  * { box-sizing: border-box; margin: 0; padding: 0; }
  html, body {
    width: 1200px; height: 800px; overflow: hidden;
    background: var(--backdrop);
    font-family: "Source Sans 3", "Source Sans Pro", Arial, sans-serif;
  }
  .card {
    position: absolute; left: 100px; top: 114px;
    width: 1000px; height: 572px;
    background: linear-gradient(170deg, var(--card-top) 0%, #e2e3e5 45%, var(--card-bottom) 100%);
    box-shadow: 0 10px 30px rgba(0,0,0,.18);
    overflow: hidden;
  }
  .skyline {
    position: absolute; left: 0; top: 60px; width: 1000px; height: 175px;
    background: linear-gradient(180deg, rgba(211,213,216,0) 0%, var(--skyline) 60%, #c8cacd 100%);
  }
  .brand {
    position: absolute; left: 470px; top: 80px;
    display: flex; align-items: center; gap: 16px;
  }
  .brand-mark { width: 26px; height: 26px; background: var(--accent); }
  .brand-name {
    font-weight: 700; font-size: 46px; letter-spacing: 3px; color: var(--band);
  }
  .licence {
    position: absolute; right: 44px; top: 120px;
    font-size: 26px; letter-spacing: 2px; color: var(--ink-soft);
  }
  .band {
    position: absolute; left: 0; top: 235px; width: 100%; height: 58px;
    background: var(--band);
    display: flex; align-items: center; padding-left: 60px; gap: 26px;
  }
  .person-name { color: var(--accent); font-size: 34px; font-weight: 400; letter-spacing: 1px; }
  .person-role { color: var(--band-text); font-size: 32px; letter-spacing: 1px; }
  .contacts {
    position: absolute; top: 330px; list-style: none;
    font-size: 27px; color: var(--ink); line-height: 46px;
  }
  .contacts li { display: flex; align-items: center; gap: 22px; }
  .contacts svg { width: 24px; height: 24px; flex: none; }
  .contacts-phone { left: 60px; }
  .contacts-office { left: 440px; }
  .icon { fill: var(--accent); }
</style>
</head>
<body>
<article class="card">
  <div class="skyline" role="img" aria-label="Grey silhouette of a city skyline with a suspension bridge"></div>

  <div class="brand">
    <span class="brand-mark"></span>
    <span class="brand-name">BROCK CONSTRUCTION</span>
  </div>
  <p class="licence">LIC 514387</p>

  <div class="band">
    <span class="person-name">WARREN "BROCK" PELKEY</span>
    <span class="person-role">CONTRACTOR</span>
  </div>

  <ul class="contacts contacts-phone">
    <li><svg viewBox="0 0 24 24"><rect class="icon" x="5" y="1" width="14" height="22" rx="3"/><rect x="8" y="4" width="8" height="13" fill="#fff"/></svg>(415) 736-4052</li>
    <li><svg viewBox="0 0 24 24"><circle class="icon" cx="12" cy="12" r="11"/><path d="M8 6c-2 3 0 9 6 12l2-2-3-2-1 1c-2-1-3-3-3-5l1-1-1-3z" fill="#fff"/></svg>(650) 514-2087</li>
    <li><svg viewBox="0 0 24 24"><rect class="icon" x="2" y="2" width="20" height="20" rx="2"/><rect x="6" y="5" width="12" height="6" fill="#fff"/><rect x="6" y="14" width="12" height="5" fill="#fff"/></svg>(650) 514-2088</li>
  </ul>

  <ul class="contacts contacts-office">
    <li><svg viewBox="0 0 24 24"><circle class="icon" cx="12" cy="12" r="11"/><rect x="6" y="8" width="12" height="8" fill="#fff"/><path d="M6 8l6 5 6-5" stroke="#1f9be0" stroke-width="1.5" fill="none"/></svg>brock@brockconstruction.example</li>
    <li><svg viewBox="0 0 24 24"><path class="icon" d="M12 1a8 8 0 0 0-8 8c0 6 8 14 8 14s8-8 8-14a8 8 0 0 0-8-8z"/><circle cx="12" cy="9" r="3" fill="#fff"/></svg>Lic 514387, 3148 Larkspur Row</li>
    <li><svg viewBox="0 0 24 24"></svg>San Bruno, California 94071</li>
    <li><svg viewBox="0 0 24 24"><circle class="icon" cx="12" cy="12" r="11"/><path d="M1 12h22M12 1v22M5 5c4 3 10 3 14 0M5 19c4-3 10-3 14 0" stroke="#fff" stroke-width="1.4" fill="none"/><ellipse cx="12" cy="12" rx="5" ry="11" stroke="#fff" stroke-width="1.4" fill="none"/></svg>www.brockconstruction.example</li>
  </ul>
</article>
</body>
</html>
```